Building company buisness cards

We are looking for a sharp modern new look for our business cards.
We are a New Zealand based company that specialises in house and land packages.
We have attached a photo of the current logo and would like to see if it can be improved somehow if needed.
We are open to any colours but we have chosen green at this stage.
Feel free to change the font and make the logo smarter looking.
Play with the colours and see what looks best.

We want a card that looks so good know one will want to throw it away!

Target Market(s)

Home buyers

Industry/Entity Type

Building

Contact Information for Business Card

Derek Tolvane
0217394062
dtolvane@quillmarkhomesteads.co.nz
quillmarkhomesteads.co.nz

Font styles to use
Serif
Sans Serif

Colors

Designer to choose colors to be used in the design.

Requirements
Must have
• Logo and company name on one side, details on the other side
Nice to have
• Color codes for the original green are HEX #4a8028, RGB(74,128,40), CMYK(42,0,69,50)
• Round corners, Raised and/or spot UV

```html
<!DOCTYPE html>
<html lang="en">
<head>
<meta charset="utf-8">
<title>Quillmark Homesteads — Business Card</title>
<link rel="stylesheet" href="https://fonts.googleapis.com/css2?family=Cinzel:wght@500;600&family=Nunito+Sans:wght@300;400;800&display=swap">
<style>
  :root {
    --brand-green: #4a8028;
    --brand-green-soft: #5a9233;
    --ink-grey: #555555;
    --rule-grey: #9a9a9a;
    --paper: #ffffff;
    --backdrop: #232323;
  }
  * { margin: 0; padding: 0; box-sizing: border-box; }
  html, body {
    width: 1125px;
    height: 1200px;
    overflow: hidden;
    background: var(--backdrop);
  }
  .canvas {
    position: relative;
    width: 1125px;
    height: 1200px;
  }
  .card {
    position: absolute;
    left: 145px;
    width: 800px;
    height: 457px;
    overflow: hidden;
  }
  .card--front { top: 95px; background: var(--paper); }
  .card--back { top: 612px; background: var(--brand-green); }

  .brand-name {
    position: absolute;
    right: 58px;
    top: 140px;
    text-align: left;
    font-family: "Cinzel", serif;
    font-weight: 600;
    color: var(--brand-green);
    font-size: 40px;
    line-height: 1.0;
    letter-spacing: 0.5px;
  }
  .contact {
    position: absolute;
    left: 40px;
    top: 298px;
  }
  .contact__name {
    font-family: "Cinzel", serif;
    font-weight: 600;
    color: var(--brand-green);
    font-size: 31px;
    letter-spacing: 1.5px;
    margin-bottom: 10px;
  }
  .contact__line {
    font-family: "Nunito Sans", sans-serif;
    font-weight: 300;
    color: var(--ink-grey);
    font-size: 18px;
    line-height: 27px;
  }
  .footer-bands {
    position: absolute;
    left: 0;
    bottom: 0;
    width: 800px;
    height: 48px;
  }
  .footer-web {
    position: absolute;
    right: 20px;
    bottom: 8px;
    font-family: "Nunito Sans", sans-serif;
    font-weight: 300;
    color: var(--paper);
    font-size: 18px;
  }

  .back-art {
    position: absolute;
    left: 6px;
    top: 10px;
    width: 515px;
    height: 447px;
    background: linear-gradient(180deg, var(--brand-green-soft), var(--brand-green));
  }
  .back-wordmark {
    position: absolute;
    right: 72px;
    top: 48px;
    writing-mode: vertical-rl;
    font-family: "Nunito Sans", sans-serif;
    font-weight: 800;
    color: var(--paper);
    font-size: 40px;
    line-height: 46px;
    letter-spacing: 0.5px;
  }
</style>
</head>
<body>
<main class="canvas">

  <section class="card card--front" aria-label="Card front">
    <div class="brand-name">QUILLMARK<br>HOMESTEADS.</div>

    <div class="contact">
      <h1 class="contact__name">DEREK TOLVANE</h1>
      <p class="contact__line">0217394062</p>
      <p class="contact__line">dtolvane@quillmarkhomesteads.co.nz</p>
    </div>

    <svg class="footer-bands" viewBox="0 0 800 48" aria-hidden="true">
      <path d="M0 17 H450 Q443 28 428 29 H0 Z" fill="var(--rule-grey)"/>
      <rect x="0" y="34" width="800" height="14" fill="var(--brand-green)"/>
      <path d="M470 48 L458 48 Q452 10 475 8 H800 V48 Z" fill="var(--brand-green)"/>
    </svg>
    <div class="footer-web">www.quillmarkhomesteads.co.nz</div>
  </section>

  <section class="card card--back" aria-label="Card back">
    <div class="back-art" role="img" aria-label="Large white family figures illustration"></div>
    <div class="back-wordmark">quillmark<br>homesteads.</div>
  </section>

</main>
</body>
</html>
```